Heron Loan Partners Business Card

We need a business card design for our mortgage servicing company. In addition to servicing the loans of homeowners, we help homeowners with purchasing their homes and any mortgage refinancing. We would like to see designs that use the colors in the logo attached below (gold-ish yellow and navy blue), and any other design you deem fit! The design should communicate a simpler life with smart mortgages provided by Heron.

```html
<!DOCTYPE html>
<html lang="en">
<head>
<meta charset="utf-8">
<title>Heron Loan Partners Business Card</title>
<link href="https://fonts.googleapis.com/css2?family=Montserrat:wght@400;600;700&display=swap" rel="stylesheet">
<style>
  :root {
    --gold: #e0b33c;
    --navy: #25215a;
    --white: #ffffff;
    --stage: #232323;
  }
  * { margin: 0; padding: 0; box-sizing: border-box; }
  html, body {
    width: 1200px; height: 880px; overflow: hidden;
    background: var(--stage);
    font-family: "Montserrat", Arial, sans-serif;
  }
  .canvas { position: relative; width: 1200px; height: 880px; }
  .card {
    position: absolute; width: 560px; height: 320px;
    background: var(--white); overflow: hidden;
    box-shadow: 0 10px 24px rgba(0,0,0,0.45);
  }
  .card--front { left: 90px; top: 120px; }
  .card--back { left: 550px; top: 470px; }

  .brand {
    position: absolute; display: flex; align-items: center; gap: 12px;
    color: var(--navy); font-weight: 700; white-space: nowrap;
  }
  .brand__dot { border-radius: 50%; background: var(--gold); flex: none; }
  .card--front .brand { left: 50%; top: 50%; transform: translate(-50%, -50%); font-size: 36px; }
  .card--front .brand__dot { width: 30px; height: 30px; }
  .card--back .brand { left: 36px; top: 66px; font-size: 20px; gap: 9px; }
  .card--back .brand__dot { width: 16px; height: 16px; }

  .wave { position: absolute; inset: 0; width: 560px; height: 320px; }

  .contact {
    position: absolute; right: 28px; top: 96px; width: 240px;
    text-align: right; color: var(--white);
  }
  .contact__name { font-weight: 700; font-size: 16px; letter-spacing: 0.5px; }
  .contact__role { font-size: 12px; margin: 2px 0 14px; }
  .contact__address { font-size: 11.5px; line-height: 1.4; margin-bottom: 6px; }
  .contact__line {
    display: flex; justify-content: flex-end; align-items: center; gap: 8px;
    font-size: 11.5px; line-height: 1.75;
  }
  .contact__line svg { width: 12px; height: 12px; flex: none; }
</style>
</head>
<body>
<div class="canvas">

  <section class="card card--front" aria-label="Card front">
    <div class="brand"><span class="brand__dot"></span><span>Heron Loan Partners</span></div>
  </section>

  <section class="card card--back" aria-label="Card back">
    <svg class="wave" viewBox="0 0 560 320" aria-hidden="true">
      <defs>
        <path id="wave-edge" d="M-40,262 C100,256 195,226 245,160 C285,100 325,38 415,18 C465,8 520,8 620,6 L620,360 L-40,360 Z"/>
      </defs>
      <use href="#wave-edge" fill="var(--gold)"/>
      <use href="#wave-edge" fill="var(--white)" transform="translate(4,6)"/>
      <use href="#wave-edge" fill="var(--navy)" transform="translate(8,11)"/>
      <use href="#wave-edge" fill="var(--white)" transform="translate(24,26)"/>
      <use href="#wave-edge" fill="var(--gold)" transform="translate(27,30)"/>
    </svg>

    <div class="brand"><span class="brand__dot"></span><span>Heron Loan Partners</span></div>

    <div class="contact">
      <p class="contact__name">DANA WHITFIELD</p>
      <p class="contact__role">Owner</p>
      <p class="contact__address">482 Larkspur Ave, Ste<br>210, Austin, TX 78701</p>
      <p class="contact__line">555.014.2286
        <svg viewBox="0 0 12 12"><path d="M2 4.5C2 3 3.5 2 6 2s4 1 4 2.5L8.5 5 8 4H4L3.5 5Z M3 6h6l1 4H2Z" fill="var(--white)"/></svg>
      </p>
      <p class="contact__line">info@heronloanpartners.com
        <svg viewBox="0 0 12 12"><rect x="1" y="3" width="10" height="7" fill="var(--white)"/><path d="M1 3l5 4 5-4" fill="none" stroke="var(--gold)" stroke-width="1"/></svg>
      </p>
      <p class="contact__line">www.heronloanpartners.com
        <svg viewBox="0 0 12 12"><circle cx="6" cy="6" r="5" fill="var(--white)"/><path d="M1 6h10M6 1c-2 2.5-2 7.5 0 10M6 1c2 2.5 2 7.5 0 10" fill="none" stroke="var(--gold)" stroke-width="0.8"/></svg>
      </p>
    </div>
  </section>

</div>
</body>
</html>
```